Home Staging Company needs business card design

We're a home staging company called Brightly Settled Home Staging. We would like a business card design that includes aqua and gray. Our current logo of house within chair is fine but I find we almost always use the logo in one color. I'll upload images of front and back of our current card and our logo. Note that we have dropped "Solutions" from our company name and don't want to include it on the card.

Target Market(s)

Realtors and homeowners - people interested in selling their homes

Contact Information for Business Card

Marisol Thistlewood
Brightly Settled Home Staging
757-555-0193
www.brightlysettled.com
marisol@brightlysettled.com

Font styles to use
Serif
Script

Requirements
Must have
• My logo and contact details
• UPDATE***
• I forgot to say that the company name should be included on the front of the card somehow.

```html
<!DOCTYPE html>
<html lang="en">
<head>
<meta charset="utf-8">
<title>Brightly Settled Home Staging — Business Card</title>
<link rel="stylesheet" href="https://fonts.googleapis.com/css2?family=Playfair+Display:wght@700&family=Quicksand:wght@500;600&display=swap">
<style>
  :root {
    --backdrop: #3a3a3b;
    --card: #1f1f21;
    --card-edge: #2a2a2c;
    --aqua: #56b9c4;
    --gray-band: #4a4f55;
    --white: #f4f6f7;
    --muted: #b9bec2;
    --emboss: #4a4a4d;
  }
  * { margin: 0; padding: 0; box-sizing: border-box; }
  html, body { width: 799px; height: 1200px; overflow: hidden; }
  body {
    background: var(--backdrop);
    font-family: "Quicksand", sans-serif;
    position: relative;
  }
  .card {
    position: absolute;
    left: 80px;
    width: 640px;
    height: 366px;
    background: var(--card);
    border: 1px solid var(--card-edge);
    border-radius: 4px;
    box-shadow: 0 14px 30px rgba(0,0,0,.45);
    overflow: hidden;
  }
  .card--front { top: 150px; }
  .card--back { top: 690px; }

  /* Front */
  .front-mark {
    position: absolute;
    inset: 0;
    display: flex;
    align-items: center;
    justify-content: center;
    gap: 18px;
  }
  .front-mark__dot {
    width: 46px; height: 46px;
    border-radius: 50%;
    background: var(--emboss);
  }
  .front-mark__name {
    font-family: "Playfair Display", serif;
    font-weight: 700;
    font-size: 34px;
    line-height: 1.1;
    color: var(--emboss);
  }

  /* Back */
  .brand {
    position: absolute;
    left: 40px; top: 38px;
    display: flex;
    align-items: center;
    gap: 16px;
  }
  .brand__dot {
    width: 58px; height: 58px;
    border-radius: 50%;
    background: var(--aqua);
  }
  .brand__name {
    font-family: "Playfair Display", serif;
    font-weight: 700;
    font-size: 27px;
    line-height: 1.15;
    color: var(--white);
  }
  .person {
    position: absolute;
    left: 40px; top: 168px;
  }
  .person__name {
    font-size: 23px;
    font-weight: 500;
    color: var(--white);
  }
  .person__name span { color: var(--aqua); }
  .person__title {
    margin-top: 4px;
    font-size: 12px;
    font-weight: 500;
    color: var(--muted);
  }
  .contacts {
    position: absolute;
    left: 320px; top: 196px;
    list-style: none;
  }
  .contacts li {
    display: flex;
    align-items: center;
    gap: 12px;
    font-size: 15px;
    font-weight: 500;
    color: var(--white);
    margin-bottom: 7px;
  }
  .contacts svg { width: 15px; height: 15px; fill: var(--aqua); flex: none; }
  .band-gray {
    position: absolute;
    left: 0; right: 0; bottom: 0;
    height: 44px;
    background: var(--gray-band);
  }
  .band-aqua {
    position: absolute;
    right: 0; bottom: 0;
    width: 380px; height: 58px;
    background: var(--aqua);
    border-top-left-radius: 28px;
    display: flex;
    align-items: center;
    justify-content: center;
    color: var(--white);
    font-size: 16px;
    font-weight: 600;
  }
</style>
</head>
<body>

  <section class="card card--front" aria-label="Card front">
    <div class="front-mark">
      <div class="front-mark__dot"></div>
      <div class="front-mark__name">Brightly Settled<br>Home Staging</div>
    </div>
  </section>

  <section class="card card--back" aria-label="Card back">
    <div class="brand">
      <div class="brand__dot"></div>
      <div class="brand__name">Brightly Settled<br>Home Staging</div>
    </div>

    <div class="person">
      <p class="person__name">Marisol <span>Thistlewood</span></p>
      <p class="person__title">Managing Director</p>
    </div>

    <ul class="contacts">
      <li>
        <svg viewBox="0 0 16 16" aria-hidden="true"><path d="M2 5c0-2 2-3 3-3l1 3-1.5 1.5c.8 1.8 2.2 3.2 4 4L10 9l3 1c0 1-1 3-3 3C5.5 13 2 9.5 2 5z"/></svg>
        757-555-0193
      </li>
      <li>
        <svg viewBox="0 0 16 16" aria-hidden="true"><path d="M8 1a7 7 0 1 0 0 14A7 7 0 0 0 8 1zm0 1.5c.8 0 1.7 1.7 1.9 4.5H6.1C6.3 4.2 7.2 2.5 8 2.5zM2.6 7h2.2c.1-1.6.4-3 .9-3.9A5.6 5.6 0 0 0 2.6 7zm0 2a5.6 5.6 0 0 0 3.1 3.9c-.5-.9-.8-2.3-.9-3.9H2.6zm3.5 0c.2 2.8 1.1 4.5 1.9 4.5s1.7-1.7 1.9-4.5H6.1zm5.1 0c-.1 1.6-.4 3-.9 3.9A5.6 5.6 0 0 0 13.4 9h-2.2zm2.2-2a5.6 5.6 0 0 0-3.1-3.9c.5.9.8 2.3.9 3.9h2.2z"/></svg>
        www.brightlysettled.com
      </li>
      <li>
        <svg viewBox="0 0 16 16" aria-hidden="true"><path d="M1 3.5h14v9H1zm1.5 1.3v.3L8 9l5.5-3.9v-.3zm0 2.1v4.1h11V6.9L8 10.8z"/></svg>
        marisol@brightlysettled.com
      </li>
    </ul>

    <div class="band-gray"></div>
    <div class="band-aqua">Schedule a consultation today!</div>
  </section>

</body>
</html>
```